Dental Business Card Design w/logo

Classic, elegant w/a touch of contemporary
Upscale dental facility located in Modesto CA
Specializing in restorative & general dentistry
Providing exceptional customer service to the community
Updates

I prefer script and not bold writing
If you can use the phone; fax and email icons instead of spelling them out, it would be great
No bold colors
Classy and elegant
In the back of the card I would like to see something like this
Your Next Appointment:
Mon     Tue    Wed    Thur (a box next to each of them for marking)
Date:_______________ at_____________ AM    PM  (a box next to them for marking)

Thank you

Target Market(s)

Well established professional

Industry/Entity Type

Dental

Contact Information for Business Card

Velarina Tossudi DMD
4176 Marlow Rd
Suite K7
Modesto, CA 95418

Office: 209-731-5920
Fax: 209-731-8047
Email: tossudidmd@quillmail.example

Requirements
Must have
• Unique classic logo
An easily repeatable design that can be used on letterhead and envelopes
Nice to have
• My initials incorporated into unique design
Should not have
• No cartoons or cheesy themes. This is a practice for the well established and professional individual.

```html
<!DOCTYPE html>
<html lang="en">
<head>
<meta charset="utf-8">
<title>Velarina Tossudi DMD – Business Card</title>
<link rel="stylesheet" href="https://fonts.googleapis.com/css2?family=Cormorant+Garamond:ital,wght@0,400;0,500;1,400&display=swap">
<style>
  :root {
    --backdrop: #e6e7e8;
    --card: #ffffff;
    --ink: #3a3a3a;
    --ink-soft: #5a5a5a;
    --aqua: #8fd3d6;
    --aqua-deep: #6cc3c7;
    --shadow: rgba(0, 0, 0, 0.18);
  }
  * { box-sizing: border-box; margin: 0; padding: 0; }
  html, body {
    width: 1200px;
    height: 560px;
    overflow: hidden;
    background: var(--backdrop);
  }
  .stage {
    width: 1200px;
    height: 560px;
    display: flex;
    align-items: center;
    justify-content: center;
  }
  .card {
    position: relative;
    width: 290px;
    height: 500px;
    background: var(--card);
    box-shadow: 0 6px 24px var(--shadow);
    font-family: "Cormorant Garamond", Georgia, serif;
    color: var(--ink);
  }
  .brand {
    position: absolute;
    top: 112px;
    left: 58px;
    display: flex;
    align-items: center;
    gap: 10px;
  }
  .brand-dot {
    width: 14px;
    height: 14px;
    border-radius: 50%;
    background: var(--aqua);
  }
  .brand-name {
    font-size: 22px;
    font-weight: 400;
    color: var(--aqua-deep);
    letter-spacing: 0.5px;
  }
  .identity {
    position: absolute;
    top: 232px;
    left: 46px;
  }
  .doctor-name {
    font-size: 15px;
    font-weight: 500;
    text-transform: uppercase;
    letter-spacing: 1.6px;
    white-space: nowrap;
  }
  .specialty {
    margin-top: 3px;
    font-size: 13px;
    font-style: italic;
    color: var(--ink-soft);
    letter-spacing: 0.3px;
  }
  .contact {
    position: absolute;
    top: 356px;
    left: 58px;
    font-size: 14px;
    font-style: italic;
    line-height: 1.3;
    letter-spacing: 0.6px;
  }
  .contact .phones { margin-top: 6px; }
  .label { color: var(--aqua-deep); margin-right: 6px; }
  .email {
    margin-top: 10px;
    color: var(--aqua-deep);
  }
</style>
</head>
<body>
  <main class="stage">
    <article class="card">
      <div class="brand">
        <span class="brand-dot"></span>
        <span class="brand-name">Tossudi Dental</span>
      </div>

      <header class="identity">
        <h1 class="doctor-name">Velarina Tossudi, D.M.D.</h1>
        <p class="specialty">Restorative &amp; General Dentistry</p>
      </header>

      <address class="contact">
        <p>4176 Marlow Rd. Suite K7</p>
        <p>Modesto, CA 95418</p>
        <div class="phones">
          <p><span class="label">T:</span>209 731 5920</p>
          <p><span class="label">F:</span>209 731 8047</p>
        </div>
        <p class="email">tossudidmd@quillmail.example</p>
      </address>
    </article>
  </main>
</body>
</html>
```